Blue Harbor Inc - Cutting-Edge Biotech Laboratory - Sleek & Sophisticated

Please design a website that has more of a high-tech and high-end feel, with contents outlined in the uploaded file.

Please have main tabs of the following categories: Home, About, FDA & LAWS, Science, Products, Media, Contact.

Media can include all the videos and photos.

Current website: www.blueharborlabs.com - it needs to be much more high-end, sleek and more organized. Please do NOT follow the outlines in the old website, but follow the uploaded CONTENT file.

Target Market(s)

doctors

Industry/Entity Type

Biotechnology

Coding

Coded - Design and coding required

Number of Pages Required

5+ page

Requirements
Must have
• Logo
Nice to have
• Some lotion on the website

```html
<!DOCTYPE html>
<html lang="en">
<head>
<meta charset="utf-8">
<title>Blue Harbor – Regenerative Medicine</title>
<link href="https://fonts.googleapis.com/css2?family=Montserrat:wght@400;500;600&family=Open+Sans:ital,wght@0,400;0,600;1,400&display=swap" rel="stylesheet">
<style>
:root{
  --gold:#b8913f;
  --gold-light:#e0a640;
  --ink:#222222;
  --text:#555555;
  --muted:#777777;
  --band:#f1f1f1;
  --white:#ffffff;
  --footer:#1c1916;
  --ring:#9a9a9a;
}
*{box-sizing:border-box;margin:0;padding:0}
html,body{width:1200px;height:3291px;overflow:hidden}
body{position:relative;background:var(--white);font-family:"Open Sans",Arial,sans-serif;color:var(--text)}
.abs{position:absolute}
.heading{font-family:"Montserrat",Arial,sans-serif;color:var(--ink);font-weight:500;letter-spacing:1px;font-size:30px;text-transform:uppercase}
.center{left:0;width:1200px;text-align:center}

/* hero */
.hero{left:0;top:0;width:1200px;height:597px;overflow:hidden;
  background:
   radial-gradient(circle at 585px 250px,#ffb070 0,#f57a3c 55px,#e2603a 105px,rgba(90,150,215,.95) 150px,rgba(40,95,165,.9) 190px,transparent 215px),
   radial-gradient(circle at 600px 255px,rgba(160,210,255,.55) 0,rgba(160,210,255,.35) 215px,transparent 240px),
   linear-gradient(180deg,transparent 0,transparent 230px,rgba(200,225,250,.35) 260px,rgba(200,225,250,.5) 285px,rgba(200,225,250,.2) 305px,transparent 330px),
   radial-gradient(ellipse at 20% 20%,#6f9cc8 0,transparent 55%),
   radial-gradient(ellipse at 85% 15%,#5f8cbc 0,transparent 50%),
   linear-gradient(180deg,#4678b0 0%,#244f86 55%,#163a6a 100%)}
.logo{left:99px;top:44px;font-family:"Montserrat",Arial,sans-serif;font-size:30px;font-weight:500;color:var(--white);letter-spacing:1px}
.nav{right:97px;top:54px;display:flex;align-items:center;gap:24px;font-family:"Montserrat",Arial,sans-serif;font-size:14px;font-weight:500;color:var(--white);letter-spacing:.5px}
.nav .active{color:var(--gold-light)}
.hero-title{top:230px;font-family:"Montserrat",Arial,sans-serif;font-size:48px;line-height:66px;font-weight:500;color:var(--white);text-shadow:0 2px 10px rgba(0,0,0,.25)}
.dots{top:535px;left:566px;display:flex;gap:5px}
.dots span{width:13px;height:13px;border-radius:50%;border:2px solid var(--white)}
.dots span.on{background:var(--white)}

/* welcome */
.welcome-title{left:99px;top:680px}
.welcome-text{left:99px;top:744px;width:480px;font-size:13.5px;line-height:27px}
.btn{display:flex;align-items:center;justify-content:center;border:2px solid var(--gold);color:var(--gold);font-family:"Montserrat",Arial,sans-serif;font-weight:600;font-size:13px;letter-spacing:.5px;width:125px;height:44px}
.video{left:611px;top:689px;width:491px;height:325px;
  background:
   radial-gradient(ellipse 45px 120px at 50% 35%,#b8c8f0 0,#8a9ad8 50%,transparent 100%),
   radial-gradient(ellipse at 26% 60%,#f3efe4 0,#e6dfcc 18%,transparent 32%),
   radial-gradient(ellipse at 78% 62%,#f3efe4 0,#e6dfcc 16%,transparent 30%),
   radial-gradient(ellipse at 50% 85%,#6a2a20 0,#5a2a1e 25%,transparent 55%),
   linear-gradient(180deg,#efe4c8 0%,#e2d2ae 55%,#8a4a2e 82%,#5a2e1e 100%)}

/* clinical */
.band{left:0;width:1200px;background:var(--band)}
.app{width:206px;text-align:center;font-family:"Montserrat",Arial,sans-serif;font-size:20px;color:var(--ink);font-weight:500}
.app .ring{width:180px;height:180px;border:1.5px solid var(--ring);border-radius:50%;margin:0 auto 28px;display:flex;align-items:center;justify-content:center}

/* services */
.service{width:316px;text-align:center}
.service .photo{width:316px;height:235px;border:4px solid var(--white);box-shadow:0 0 0 1px #ddd}
.service p{margin-top:28px;font-family:"Montserrat",Arial,sans-serif;font-size:20px;line-height:31px;color:var(--ink);font-weight:500}

/* research */
.research-photo{left:99px;top:2108px;width:439px;height:310px;
  background:
   radial-gradient(ellipse 60px 110px at 36% 30%,#f4f6ee 0,#d8e0d0 55%,transparent 100%),
   radial-gradient(ellipse at 18% 70%,#2a2a30 0,transparent 35%),
   radial-gradient(ellipse at 62% 72%,#26262c 0,transparent 30%),
   radial-gradient(ellipse at 82% 70%,#2a2a2e 0,transparent 32%),
   linear-gradient(180deg,#a8703e 0%,#8a5a36 45%,#5a4434 100%)}
.research-title{left:621px;top:2142px}
.research-text{left:621px;top:2196px;width:460px;font-size:13.5px;line-height:27px}

/* team */
.member{width:260px;text-align:center}
.member .portrait{width:232px;height:232px;border-radius:50%;margin:0 auto;border:5px solid var(--white);box-shadow:0 0 0 1px #ddd}
.member h3{margin-top:20px;font-family:"Montserrat",Arial,sans-serif;font-size:20px;font-weight:500;color:var(--ink)}
.member p{margin-top:6px;font-size:14px;font-style:italic;line-height:22px;color:var(--muted)}
.arrow{top:2696px}

/* footer */
.footer{left:0;top:2999px;width:1200px;height:292px;background:var(--footer);color:var(--white)}
.footer-logo{top:54px;font-family:"Montserrat",Arial,sans-serif;font-size:40px;font-weight:500;letter-spacing:1px}
.social{top:120px;left:507px;display:flex;gap:9px}
.social span{width:40px;height:40px;border:1.5px solid var(--white);border-radius:50%}
.footer-links{top:180px;font-size:16px}
.footer-links span{margin:0 10px}
.copyright{top:222px;font-size:16px}
</style>
</head>
<body>

<section class="abs hero" role="img" aria-label="Microscope close-up of a glowing cell being reached by a fine glass pipette on a deep blue background">
  <div class="abs logo">BLUE HARBOR</div>
  <nav class="abs nav">
    <span class="active">HOME</span><span>ABOUT</span><span>FDA &amp; LAWS</span><span>SCIENCE</span><span>PRODUCTS</span><span>MEDIA</span><span>CONTACT</span>
    <svg width="16" height="16" viewBox="0 0 16 16" aria-hidden="true"><circle cx="6.5" cy="6.5" r="4.5" fill="none" stroke="#fff" stroke-width="2.2"/><line x1="10" y1="10" x2="14.5" y2="14.5" stroke="#fff" stroke-width="2.5"/></svg>
  </nav>
  <h1 class="abs center hero-title">Leader in Regenerative<br>Medicine Innovator of the Industry</h1>
  <div class="abs dots"><span class="on"></span><span></span><span></span><span></span></div>
</section>

<section>
  <h2 class="abs heading welcome-title">Welcome to Blue Harbor</h2>
  <p class="abs welcome-text">Blue Harbor Therapy provides Non-Embryonic Stem Cells and unique protocols to doctors in order to help their patients who face major health conditions, as well as those who simply wish to stay young and healthy. Over the past seven years of development, we have successfully conducted research into major diseases related to kidney, liver and heart failures, and have aided in helping people who have suffered stroke or brain injury to walk or talk again.</p>
  <div class="abs btn" style="left:99px;top:970px">READ MORE</div>
  <div class="abs video" role="img" aria-label="Video still of an interview with two people seated in cream armchairs in a bright room"></div>
  <svg class="abs" style="left:826px;top:821px" width="60" height="60" viewBox="0 0 60 60" aria-hidden="true"><circle cx="30" cy="30" r="30" fill="rgba(20,20,20,.8)"/><path d="M24 18 L42 30 L24 42 Z" fill="#fff"/></svg>
</section>

<section class="abs band" style="top:1101px;height:435px"></section>
<h2 class="abs heading center" style="top:1168px">A Wide Variety of Clinical Applications</h2>
<div class="abs app" style="left:86px;top:1246px"><div class="ring">
  <svg width="100" height="100" viewBox="0 0 80 80" aria-hidden="true"><rect x="30" y="4" width="14" height="32" rx="6" fill="var(--gold)" transform="rotate(-15 37 20)"/><rect x="33" y="42" width="14" height="34" rx="6" fill="var(--gold)" transform="rotate(10 39 58)"/><circle cx="40" cy="40" r="8" fill="none" stroke="var(--gold)" stroke-width="3"/></svg>
</div>Orthopedics</div>
<div class="abs app" style="left:292px;top:1246px"><div class="ring">
  <svg width="100" height="100" viewBox="0 0 80 80" aria-hidden="true"><rect x="28" y="14" width="24" height="12" rx="3" fill="none" stroke="var(--gold)" stroke-width="4"/><rect x="10" y="24" width="60" height="44" rx="5" fill="var(--gold)"/><path d="M34 34h12v8h8v12h-8v8H34v-8h-8V42h8z" fill="#fff" transform="translate(0 -4)"/></svg>
</div>Sports Medicine</div>
<div class="abs app" style="left:496px;top:1246px"><div class="ring">
  <svg width="100" height="100" viewBox="0 0 80 80" aria-hidden="true"><rect x="26" y="6" width="28" height="68" rx="14" fill="var(--gold)" transform="rotate(45 40 40)"/><rect x="26" y="6" width="28" height="68" rx="14" fill="var(--gold)" opacity=".8" transform="rotate(-45 40 40)"/><rect x="31" y="31" width="18" height="18" fill="#fff" transform="rotate(45 40 40)"/></svg>
</div>Wound Care</div>
<div class="abs app" style="left:702px;top:1246px"><div class="ring">
  <svg width="100" height="100" viewBox="0 0 80 80" aria-hidden="true"><path d="M30 24c10-4 22 2 22 16 0 10-4 14-4 22 0 8-4 12-10 12s-10-6-9-14c1-8-6-14-5-24 1-6 2-10 6-12z" fill="var(--gold)"/><circle cx="28" cy="10" r="5" fill="var(--gold)"/><circle cx="38" cy="9" r="3.5" fill="var(--gold)"/><circle cx="45" cy="12" r="3" fill="var(--gold)"/><circle cx="51" cy="16" r="2.5" fill="var(--gold)"/></svg>
</div>Podiatry</div>
<div class="abs app" style="left:906px;top:1246px"><div class="ring">
  <svg width="100" height="100" viewBox="0 0 80 80" aria-hidden="true"><path d="M22 70V54c-8-6-12-14-10-26 3-14 16-20 28-18 14 2 22 14 20 26l6 10h-6v8c0 4-3 6-7 6h-7v10" fill="none" stroke="var(--gold)" stroke-width="4" stroke-linejoin="round"/><path d="M30 26l6 6-6 6 6 6" fill="none" stroke="var(--gold)" stroke-width="3"/></svg>
</div>Pain Management</div>

<h2 class="abs heading center" style="top:1603px">Our Services</h2>
<div class="abs service" style="left:99px;top:1674px"><div class="photo" role="img" aria-label="Glowing orange and violet cell cluster on a dark background" style="background:radial-gradient(ellipse 90px 60px at 45% 55%,#ffd080 0,#f08a3a 40%,transparent 100%),radial-gradient(ellipse 120px 80px at 55% 50%,#c060b0 0,#7a4ab0 55%,transparent 100%),radial-gradient(ellipse at 50% 50%,#3a2a6a 0,#141428 60%,#06060c 100%)"></div><p>Highest Quality<br>Umbilical Cord</p></div>
<div class="abs service" style="left:441px;top:1674px"><div class="photo" role="img" aria-label="Scientist in a white coat working at a laboratory bench" style="background:radial-gradient(ellipse 70px 90px at 28% 55%,#f6f6f2 0,#e8e8e2 60%,transparent 100%),radial-gradient(ellipse 40px 30px at 55% 62%,#e0602a 0,transparent 100%),radial-gradient(ellipse at 85% 40%,#4a4640 0,transparent 45%),linear-gradient(135deg,#d8d8d0,#b8b2a8 50%,#6a6258)"></div><p>Amniotic<br>Membrane</p></div>
<div class="abs service" style="left:783px;top:1674px"><div class="photo" role="img" aria-label="Blue microscopic view of round tissue cells" style="background:radial-gradient(circle at 58% 52%,#a8e0ff 0,#4aa0ff 14%,transparent 30%),radial-gradient(circle at 25% 30%,#3a8af0 0,transparent 22%),radial-gradient(circle at 80% 80%,#3a8af0 0,transparent 20%),radial-gradient(circle at 55% 50%,#1a50d0 0,#0c2a90 55%,#06124a 100%)"></div><p>Placental tissue-based<br>Allograft</p></div>

<section class="abs band" style="top:2062px;height:400px"></section>
<div class="abs research-photo" role="img" aria-label="Three team members in suits standing beside a lectern in a conference room"></div>
<h2 class="abs heading research-title">Research</h2>
<p class="abs research-text">Blue Harbor Inc in keenly interested in stem cell research, in areas of both laboratory and clinical studies. We strive to in understand the multitude of uses of stem cells and the ideal parameters of such usage. Contact us about possible research partnerships.</p>
<div class="abs btn" style="left:621px;top:2330px">READ MORE</div>

<h2 class="abs heading center" style="top:2530px">Team</h2>
<svg class="abs arrow" style="left:38px" width="20" height="40" viewBox="0 0 20 40" aria-hidden="true"><path d="M16 4L4 20l12 16" fill="none" stroke="#999" stroke-width="2.5"/></svg>
<svg class="abs arrow" style="left:1146px" width="20" height="40" viewBox="0 0 20 40" aria-hidden="true"><path d="M4 4l12 16L4 36" fill="none" stroke="#999" stroke-width="2.5"/></svg>
<div class="abs member" style="left:83px;top:2600px"><div class="portrait" role="img" aria-label="Portrait of the chief scientist" style="background:radial-gradient(ellipse 70px 60px at 50% 108%,#8a9098 0,#6e747c 70%,transparent 100%),radial-gradient(ellipse 45px 55px at 50% 42%,#d8b8a0 0,#c49a80 70%,transparent 100%),linear-gradient(160deg,#eef0f2,#c4c8cc)"></div><h3>Marco Delvane</h3><p>Chief Scientist</p></div>
<div class="abs member" style="left:340px;top:2600px"><div class="portrait" role="img" aria-label="Portrait of the stem cell project manager" style="background:radial-gradient(ellipse 80px 60px at 50% 108%,#2a2e38 0,#3a3e48 70%,transparent 100%),radial-gradient(ellipse 45px 55px at 50% 42%,#e0c0a8 0,#c8a08a 70%,transparent 100%),linear-gradient(160deg,#f2efe8,#cfcac0)"></div><h3>Lena Tressel</h3><p>Stem Cell Project Manager</p></div>
<div class="abs member" style="left:598px;top:2600px"><div class="portrait" role="img" aria-label="Portrait of a cardiology doctor" style="background:radial-gradient(ellipse 80px 60px at 50% 108%,#9ab8d8 0,#7a9cc4 70%,transparent 100%),radial-gradient(ellipse 45px 55px at 50% 42%,#e4c2a8 0,#cca48a 70%,transparent 100%),linear-gradient(160deg,#f2f4f6,#cfd6de)"></div><h3>Dr. Owen R. Hale</h3><p>Hale Center for Heart Vitality</p></div>
<div class="abs member" style="left:855px;top:2600px"><div class="portrait" role="img" aria-label="Portrait of a partner doctor" style="background:radial-gradient(ellipse 80px 60px at 50% 108%,#2e2e34 0,#44444a 70%,transparent 100%),radial-gradient(ellipse 45px 55px at 50% 42%,#e2bea4 0,#c49a82 70%,transparent 100%),linear-gradient(160deg,#f4f0ec,#d8cfc6)"></div><h3>Dr. Ravi Lindqvist</h3><p>2210 Harbor Crest Rd #B,<br>Bayview TX 77001</p></div>

<footer class="abs footer">
  <div class="abs center footer-logo">BLUE HARBOR</div>
  <div class="abs social"><span></span><span></span><span></span><span></span></div>
  <div class="abs center footer-links"><span>Home</span>|<span>About</span>|<span>FDA &amp; LAWS</span>|<span>Science</span>|<span>Products</span>|<span>Media</span>|<span>Contact</span></div>
  <div class="abs center copyright">© 2018, Blue Harbor. All Rights Reserved.</div>
</footer>

</body>
</html>
```